Hollendorf Business Card

This is the personal business card for Dr Mark Hollendorf and convers three area of his professional activity - all of them involve (foreign) languages:
o QRVB International Ltd - A translation company with 50 staff. Trades internationally
o WideHarbor Ltd - a global online auction marketplace for translation services (startup)
o Tonal Mosaic - cutting edge technology from the brain sciences which helps learners assimilate the sound patterns of a new language (startup)

Target Market(s)

The card needs to have a "cutting edge" feel - but for a fairly conservative audience - academics, investors.

Industry/Entity Type

Business

Requirements
Must have
• Text:
Dr Mark Hollendorf

Co-founder QRVB International Ltd (Language translation)
Founder WideHarbor Ltd (Translation marketplace)
Founder Tonal Mosaic (Language acquisition)

email: mark.oswin@velmora.co.nz
Phone: +64 21 596 3172
Twitter: @MarkOswin7

```html
<!DOCTYPE html>
<html lang="en">
<head>
<meta charset="utf-8">
<title>Hollendorf Business Card</title>
<link rel="stylesheet" href="https://fonts.googleapis.com/css2?family=Bebas+Neue&display=swap">
<style>
  :root {
    --backdrop: #2e2e2e;
    --brand-blue: #3d57a8;
    --paper: #ffffff;
    --ink-light: #ffffff;
  }
  * { margin: 0; padding: 0; box-sizing: border-box; }
  html, body {
    width: 1200px;
    height: 534px;
    overflow: hidden;
    background: var(--backdrop);
  }
  body {
    position: relative;
    font-family: "Bebas Neue", "Oswald", sans-serif;
    text-transform: uppercase;
  }
  .card {
    position: absolute;
    top: 119px;
    width: 517px;
    height: 295px;
    overflow: hidden;
  }
  .card--front {
    left: 62px;
    background: var(--brand-blue);
    color: var(--ink-light);
  }
  .card--back {
    left: 622px;
    background: var(--brand-blue);
    color: var(--ink-light);
  }

  /* Front */
  .front__name {
    position: absolute;
    left: 0; right: 0;
    top: 108px;
    text-align: center;
    font-size: 60px;
    line-height: 1;
    font-weight: 400;
    letter-spacing: 0.2px;
    white-space: nowrap;
  }
  .front__ventures {
    position: absolute;
    left: 0; right: 0;
    top: 170px;
    text-align: center;
    font-size: 13px;
    letter-spacing: 0.5px;
    white-space: nowrap;
  }
  .front__ventures .divider {
    display: inline-block;
    margin: 0 5px;
    opacity: 0.75;
  }

  /* Back */
  .back__header {
    position: absolute;
    left: 0; top: 0;
    width: 100%;
    height: 156px;
    background: var(--paper);
  }
  .back__name {
    position: absolute;
    left: 0; right: 0;
    top: 52px;
    text-align: center;
    color: var(--brand-blue);
    font-size: 58px;
    line-height: 1;
    font-weight: 400;
    white-space: nowrap;
  }
  .back__roles {
    position: absolute;
    right: 252px;
    top: 198px;
    list-style: none;
    text-align: right;
    font-size: 11.5px;
    letter-spacing: 0.3px;
    white-space: nowrap;
  }
  .back__roles li { height: 25px; line-height: 14px; }
  .back__contact {
    position: absolute;
    left: 292px;
    top: 196px;
    list-style: none;
    font-size: 16.5px;
    letter-spacing: 0.2px;
    white-space: nowrap;
  }
  .back__contact li { height: 25px; line-height: 20px; }
</style>
</head>
<body>
  <section class="card card--front">
    <h1 class="front__name">Dr Mark Hollendorf</h1>
    <p class="front__ventures">
      QRVB International Ltd<span class="divider">|</span>WideHarbor Ltd<span class="divider">|</span>Tonal Mosaic
    </p>
  </section>

  <section class="card card--back">
    <div class="back__header">
      <h2 class="back__name">Dr Mark Hollendorf</h2>
    </div>
    <ul class="back__roles">
      <li>Co-founder QRVB International Ltd (Language translation)</li>
      <li>Founder WideHarbor Ltd (Translation marketplace)</li>
      <li>Founder Tonal Mosaic (Language acquisition)</li>
    </ul>
    <ul class="back__contact">
      <li>Email: mark.oswin@velmora.co.nz</li>
      <li>Phone: +64 21 596 3172</li>
      <li>Twitter: @MarkOswin7</li>
    </ul>
  </section>
</body>
</html>
```